Email Preference Page Design

We are looking for a 2 page design for our users to edit their email preferences and submit friend referrals. You can find the fuctionality, content and text here:

https://brightvanta.mailrelayhub.example/app/linkClick/7281/5fa9c1d3b07e442b/28374615/9bd4e01a7c3f2a65

* the shipping and billing address might be different so you need to show the billing if the "same as shipping" box is not checked. It can auto-hide like the page above shows if that fits your design.

* when the "unsubscribe from all email lists" box is selected, all the other checkbox options will hide as in the example page. We need you to show us what the site will look like with and without that checkbox selected.

We want to match these two pages to the general feel of these website pages:

www.brightvanta.com
and
free.brightvanta.com

The page should be very clean and tight. Project is for design only but must be able to be implemented in html showing button and checkbox states. Technically this must be two pages for our system - one for all the user info and one for individual email referrals (see example above).

Target Market(s)

video professionals

Industry/Entity Type

Shipping

Requirements
Must have
• our logo (see numerous versions attached)
well designed header
well designed sections
clean editable text
tight layout
html friendly
easy to understand
2 pages
Nice to have
• custom checkboxes and radio buttons

```html
<!DOCTYPE html>
<html lang="en">
<head>
<meta charset="utf-8">
<title>Brightvanta – Communication Preferences</title>
<link rel="stylesheet" href="https://fonts.googleapis.com/css2?family=Exo+2:wght@400;500&family=Open+Sans:wght@400;600;700&display=swap">
<style>
:root{
  --navy:#1a2a38;
  --orange:#ff4f00;
  --orange-soft:#f28a2a;
  --field-border:#cfcfcf;
  --field-text:#666;
  --focus-fill:#f4fbfd;
  --focus-border:#9cc3d8;
  --page:#ffffff;
}
*{box-sizing:border-box;margin:0;padding:0}
html,body{width:877px;height:1200px;overflow:hidden;background:var(--page)}
body{font-family:"Open Sans",Arial,sans-serif;color:var(--navy)}
.page{position:relative;width:877px;height:1200px;overflow:hidden}
.brand{position:absolute;top:24px;left:0;width:877px;display:flex;justify-content:center;align-items:center;gap:16px}
.brand-dot{width:46px;height:46px;border-radius:50%;background:var(--orange-soft)}
.brand-name{font-family:"Exo 2",Arial,sans-serif;font-weight:500;font-size:66px;line-height:1;color:var(--navy);letter-spacing:1px}
.hero{position:absolute;top:121px;left:0;width:877px;height:174px;
  background:radial-gradient(ellipse at 45% 40%,#f0a030 0%,#d9701c 35%,#a8400f 65%,#5a1e08 90%,#200a03 100%)}
.hero-title{position:absolute;top:151px;left:0;width:877px;text-align:center;font-family:"Exo 2",Arial,sans-serif;font-weight:400;font-size:39px;line-height:51px;color:#fff;text-transform:uppercase}
.divider{position:absolute;top:389px;left:36px;width:806px;height:2px;background:var(--navy)}
.divider-badge{position:absolute;top:353px;left:406px;width:66px;height:66px;border-radius:50%;background:var(--navy)}
.required-note{position:absolute;top:372px;right:35px;font-size:12px;color:#555}
.section-flag{position:absolute;height:48px;width:373px;background:var(--navy);color:#fff;
  font-family:"Exo 2",Arial,sans-serif;font-size:24px;line-height:48px;padding-left:18px;
  clip-path:polygon(0 0,100% 0,97.6% 50%,100% 100%,0 100%)}
.field{position:absolute;height:38px;border:1px solid var(--field-border);background:#fff;
  font-family:"Open Sans",Arial,sans-serif;font-size:15px;color:var(--field-text);padding:0 10px;outline:none}
.field::placeholder{color:var(--field-text)}
.field.is-focused{background:var(--focus-fill);border-color:var(--focus-border)}
.select{position:absolute;height:38px;border:1px solid var(--field-border);background:#fff;font-size:15px;color:var(--field-text);padding-left:10px;line-height:38px}
.select-arrow{position:absolute;top:0;right:0;width:32px;height:36px;border-left:1px solid var(--field-border);display:flex;align-items:center;justify-content:center}
.zip-plus{position:absolute;font-size:13px;color:#555}
.field-hint{position:absolute;font-size:12px;color:#444}
.check{position:absolute;display:flex;align-items:flex-start;gap:8px;font-size:20px;line-height:26px}
.check-box{flex:none;width:22px;height:22px;border:2px solid var(--navy);background:#fff;margin-top:2px}
.check-label{color:#334a5c}
.check.is-warning .check-label{color:var(--orange)}
.submit-button{position:absolute;top:1084px;left:38px;width:258px;height:60px;border:none;background:var(--orange);color:#fff;
  font-family:"Open Sans",Arial,sans-serif;font-weight:600;font-size:28px;text-align:left;padding-left:30px;cursor:pointer;
  clip-path:polygon(0 0,100% 0,91% 50%,100% 100%,0 100%)}
</style>
</head>
<body>
<main class="page">
  <header>
    <div class="brand"><span class="brand-dot"></span><span class="brand-name">brightvanta</span></div>
    <div class="hero" role="img" aria-label="Warm orange light-burst background"></div>
    <h1 class="hero-title">Communication<br>Preferences</h1>
  </header>

  <div class="divider"></div>
  <div class="divider-badge"></div>
  <p class="required-note">Required Fields*</p>

  <form>
    <h2 class="section-flag" style="top:478px;left:38px">Contact Info</h2>
    <input class="field" style="top:547px;left:38px;width:372px" placeholder="First Name*">
    <input class="field is-focused" style="top:590px;left:38px;width:372px" placeholder="Last Name*">
    <input class="field" style="top:634px;left:38px;width:372px" placeholder="Email *">
    <input class="field" style="top:677px;left:38px;width:372px" placeholder="Phone">
    <input class="field" style="top:720px;left:38px;width:372px" placeholder="Address 1">
    <input class="field" style="top:764px;left:38px;width:372px" placeholder="Address 2">
    <input class="field" style="top:808px;left:38px;width:372px" placeholder="Address 3">
    <input class="field" style="top:851px;left:38px;width:372px" placeholder="City">
    <div class="select" style="top:896px;left:38px;width:372px">Select Country
      <span class="select-arrow"><svg width="12" height="9" viewBox="0 0 12 9"><path d="M0 0h12L6 9z" fill="#777"/></svg></span></div>
    <input class="field" style="top:939px;left:38px;width:372px" placeholder="State">
    <input class="field" style="top:981px;left:38px;width:166px" placeholder="11111">
    <span class="zip-plus" style="top:990px;left:215px">+</span>
    <input class="field" style="top:981px;left:233px;width:177px" placeholder="1111">
    <span class="field-hint" style="top:1023px;left:38px">Postal Code + 4</span>

    <h2 class="section-flag" style="top:478px;left:467px">Shipping Address</h2>
    <label class="check" style="top:546px;left:466px;width:340px">
      <span class="check-box"></span><span class="check-label">Billing address is same as shipping address</span></label>
    <input class="field" style="top:628px;left:466px;width:373px" placeholder="Street Address 1">
    <input class="field" style="top:672px;left:466px;width:373px" placeholder="Street Address 2">
    <input class="field" style="top:717px;left:466px;width:373px" placeholder="Street Address 3">
    <input class="field" style="top:759px;left:466px;width:373px" placeholder="City">
    <div class="select" style="top:804px;left:466px;width:373px">Select Country
      <span class="select-arrow"><svg width="12" height="9" viewBox="0 0 12 9"><path d="M0 0h12L6 9z" fill="#777"/></svg></span></div>
    <input class="field" style="top:847px;left:466px;width:167px" placeholder="State" hidden>
    <input class="field" style="top:847px;left:466px;width:373px" placeholder="State">
    <input class="field" style="top:890px;left:466px;width:167px" placeholder="44444">
    <span class="zip-plus" style="top:899px;left:643px">+</span>
    <input class="field" style="top:890px;left:661px;width:178px" placeholder="2222">
    <span class="field-hint" style="top:931px;left:467px">Postal Code + 4</span>

    <label class="check is-warning" style="top:972px;left:466px;width:373px">
      <span class="check-box"></span><span class="check-label">Unsubscribe from all email lists</span></label>

    <button class="submit-button" type="submit">Submit Now</button>
  </form>
</main>
</body>
</html>
```